Business Card for brovaLINK

Create a Business Card with an existing logo for brovaLINK AG. We are a Information Technology company that does consulting and developing SW to automate business processes. The main colors are given from the logo.

Industry/Entity Type

Business

Requirements
Nice to have
• we use a a font style Century Gothic in our documents

```html
<!DOCTYPE html>
<html lang="en">
<head>
<meta charset="utf-8">
<title>brovaLINK business card</title>
<link rel="stylesheet" href="https://fonts.googleapis.com/css2?family=Questrial&family=Oswald:wght@500&display=swap">
<style>
  :root {
    --page: #e9e6e1;
    --lime: #8dd42a;
    --lime-deep: #5fb515;
    --paper: #ffffff;
    --panel: #2e2e30;
    --panel-line: #9a9a9a;
    --ink: #2b2b2b;
    --ink-light: #f2f2f2;
    --ink-soft: #c9c9c9;
  }
  * { box-sizing: border-box; margin: 0; padding: 0; }
  html, body { width: 1200px; height: 970px; overflow: hidden; background: var(--page); }
  .canvas {
    position: relative; width: 1200px; height: 970px;
    font-family: "Questrial", "Century Gothic", sans-serif;
  }
  .card {
    position: absolute; top: 150px; width: 380px; height: 670px;
    box-shadow: 0 10px 30px rgba(0,0,0,.18);
  }
  .card-front { left: 180px; }
  .card-back { left: 640px; background: var(--paper); }
  .card svg.shape { position: absolute; inset: 0; }

  .wordmark {
    text-align: center; font-size: 40px; color: var(--ink); letter-spacing: .5px;
  }
  .front-logo { position: absolute; top: 300px; left: 0; right: 0; }
  .front-site {
    position: absolute; bottom: 150px; left: 0; right: 0; text-align: center;
    font-size: 15px; color: var(--ink); letter-spacing: .5px;
  }
  .back-logo { position: absolute; top: 46px; left: 0; right: 0; font-size: 34px; }

  .panel-content { position: absolute; top: 262px; left: 52px; right: 52px; color: var(--ink-light); }
  .person-name {
    font-family: "Oswald", "Century Gothic", sans-serif; font-weight: 500;
    font-size: 36px; line-height: 1; letter-spacing: 1px; text-transform: uppercase; white-space: nowrap;
  }
  .person-title { margin-top: 6px; font-size: 13px; letter-spacing: 3px; text-transform: uppercase; color: var(--ink-soft); }
  .rule { height: 1px; background: var(--panel-line); margin: 16px 0; }
  .contacts { display: grid; grid-template-columns: 1fr 1fr; row-gap: 12px; column-gap: 10px; font-size: 12.5px; }
  .contact { display: flex; align-items: center; gap: 8px; white-space: nowrap; }
  .contact svg { flex: none; }
  .divider-pin { display: flex; align-items: center; gap: 10px; margin: 16px 0; }
  .divider-pin .line { flex: 1; height: 1px; background: var(--panel-line); }
  .address { font-size: 15px; line-height: 1.5; letter-spacing: .5px; }
</style>
</head>
<body>
<main class="canvas">

  <section class="card card-front" aria-label="Card front">
    <svg class="shape" width="380" height="670" viewBox="0 0 380 670">
      <defs>
        <linearGradient id="limeFrame" x1="0" y1="0" x2="1" y2="1">
          <stop offset="0" stop-color="#8dd42a"/>
          <stop offset="1" stop-color="#5fb515"/>
        </linearGradient>
      </defs>
      <rect width="380" height="670" fill="url(#limeFrame)"/>
      <polygon fill="#ffffff"
        points="22,22 358,22 358,80 326,130 326,540 358,590 358,648 22,648 22,590 54,540 54,130 22,80"/>
    </svg>
    <p class="wordmark front-logo">brovaLINK</p>
    <p class="front-site">www.brovalink.ch</p>
  </section>

  <section class="card card-back" aria-label="Card back">
    <svg class="shape" width="380" height="670" viewBox="0 0 380 670">
      <polygon fill="#2e2e30"
        points="28,140 352,140 352,200 320,235 352,270 352,646 190,606 28,646 28,270 60,235 28,200"/>
    </svg>
    <p class="wordmark back-logo">brovaLINK</p>

    <div class="panel-content">
      <h1 class="person-name">Lena Marquardt</h1>
      <p class="person-title">General Manager</p>
      <div class="rule"></div>
      <div class="contacts">
        <div class="contact">
          <svg width="16" height="16" viewBox="0 0 16 16"><circle cx="8" cy="8" r="7" fill="none" stroke="currentColor"/><path d="M5.5 4.5l1.5 1.5-1 1a5 5 0 0 0 3 3l1-1 1.5 1.5-1 1.2c-3 0-6-3-6-6z" fill="currentColor"/></svg>
          <span>041 555 0192</span>
        </div>
        <div class="contact">
          <svg width="16" height="16" viewBox="0 0 16 16"><circle cx="8" cy="8" r="7" fill="none" stroke="currentColor"/><rect x="4.5" y="5.5" width="7" height="5" fill="none" stroke="currentColor"/><path d="M4.5 5.5l3.5 3 3.5-3" fill="none" stroke="currentColor"/></svg>
          <span>hello@brovalink.ch</span>
        </div>
        <div class="contact">
          <svg width="16" height="16" viewBox="0 0 16 16"><circle cx="8" cy="8" r="7" fill="none" stroke="currentColor"/><rect x="5" y="4" width="6" height="8" rx="1" fill="none" stroke="currentColor"/></svg>
          <span>041 555 0193</span>
        </div>
        <div class="contact">
          <svg width="16" height="16" viewBox="0 0 16 16"><circle cx="8" cy="8" r="7" fill="none" stroke="currentColor"/><circle cx="8" cy="8" r="4" fill="none" stroke="currentColor"/><path d="M4 8h8" stroke="currentColor"/></svg>
          <span>www.brovalink.ch</span>
        </div>
      </div>
      <div class="divider-pin">
        <span class="line"></span>
        <svg width="16" height="16" viewBox="0 0 16 16"><circle cx="8" cy="8" r="7" fill="none" stroke="currentColor"/><path d="M8 12.5s-3-3.2-3-5.5a3 3 0 0 1 6 0c0 2.3-3 5.5-3 5.5z" fill="currentColor"/></svg>
        <span class="line"></span>
      </div>
      <p class="address">27 Lindenhof Road<br>2nd building Street n.</p>
      <div class="rule"></div>
    </div>
  </section>

</main>
</body>
</html>
```